Business Card Design

I give lessons and clinics for dressage riders
I would like the design to be an outline (with broad lines) of a dressage horse and rider with in background of whole card with print over top tan or parchment card with burgundy print

Industry/Entity Type

Business

Contact Information for Business Card

Dale Ferrin
612-374-2059
Classical dressage training for the modern American
Clinics, lessons, training level -Prix St. George

Requirements
Must have
• broad lined outline of dressage horse and rider

```html
<!DOCTYPE html>
<html lang="en">
<head>
<meta charset="utf-8">
<title>Dale Ferrin – Business Card</title>
<link rel="stylesheet" href="https://fonts.googleapis.com/css2?family=Cinzel:wght@400;600&family=Arimo:wght@400&display=swap">
<style>
  :root {
    --page-bg: #e9e6e1;
    --card-light: #f3e6c9;
    --card-mid: #e8d5ad;
    --card-deep: #d9bf8e;
    --ink: #6e1a24;
    --figure-tone-a: rgba(110, 26, 36, 0.32);
    --figure-tone-b: rgba(110, 26, 36, 0.16);
  }
  html, body {
    margin: 0;
    padding: 0;
    width: 1200px;
    height: 800px;
    overflow: hidden;
    background: var(--page-bg);
  }
  .canvas {
    position: relative;
    width: 1200px;
    height: 800px;
  }
  .business-card {
    position: absolute;
    left: 100px;
    top: 115px;
    width: 1000px;
    height: 570px;
    background: linear-gradient(125deg, var(--card-light) 0%, var(--card-light) 35%, var(--card-mid) 65%, var(--card-deep) 100%);
    box-shadow: 0 10px 30px rgba(0,0,0,0.2);
    color: var(--ink);
    overflow: hidden;
  }
  .card-name {
    position: absolute;
    left: 0;
    width: 720px;
    top: 78px;
    margin: 0;
    text-align: center;
    font-family: "Cinzel", serif;
    font-weight: 400;
    font-size: 50px;
    letter-spacing: 2px;
  }
  .card-phone {
    position: absolute;
    left: 0;
    width: 720px;
    top: 158px;
    margin: 0;
    text-align: center;
    font-family: "Arimo", sans-serif;
    font-size: 30px;
    letter-spacing: 1px;
  }
  .card-services {
    position: absolute;
    left: 0;
    width: 720px;
    top: 262px;
    margin: 0;
    text-align: center;
    font-family: "Arimo", sans-serif;
    font-size: 27px;
    line-height: 1.25;
  }
  .card-services p { margin: 0; }
  .card-services .tagline { margin-bottom: 22px; }
  .card-services .service { line-height: 1.5; }
  .horse-rider-figure {
    position: absolute;
    right: 70px;
    top: 200px;
    width: 260px;
    height: 300px;
    border-radius: 46% 40% 30% 36%;
    background: radial-gradient(ellipse at 50% 45%, var(--figure-tone-a) 0%, var(--figure-tone-b) 60%, rgba(110,26,36,0) 100%);
  }
</style>
</head>
<body>
<main class="canvas">
  <section class="business-card">
    <h1 class="card-name">Dale Ferrin</h1>
    <p class="card-phone">612-374-2059</p>
    <div class="card-services">
      <p class="tagline">Classical dressage training for the<br>modern American Clinics</p>
      <p class="service">lessons</p>
      <p class="service">training level</p>
      <p class="service">Prix St. George</p>
    </div>
    <div class="horse-rider-figure" role="img" aria-label="Burgundy broad-line outline of a dressage horse and rider"></div>
  </section>
</main>
</body>
</html>
```